Custom Software Solutions

web design for a small custom programming company in Brisbane Australia. Specialize in business finance solutions, Spreadsheet Automation and programming and data analysis. The design should portray professionalism and honesty. Main applications deal with financial accounting reporting and analysis. Would like to see colors blue and purple used (but sparsely). added file is company logo. Trading name is TR Solutions, while the official company name is TR Solutions (QLD) Pty Ltd.

Target Market(s)

current clients for support
marketing tool for prospective clients

Industry/Entity Type

Business

Number of Pages Required

5+ page

Font styles to use
Sans Serif

Colors
0555a3
a54599
ffffff

Requirements
Must have
• introduction
• blog for news and tips
• previous and current clients/projects page
• contact us page with email submission form
Should not have
• social media links

```html
<!DOCTYPE html>
<html lang="en">
<head>
<meta charset="utf-8">
<title>TR Solutions — Custom Software Solutions</title>
<link rel="stylesheet" href="https://fonts.googleapis.com/css2?family=Open+Sans:wght@400;600&display=swap">
<style>
:root{
  --blue:#0555a3;
  --blue-dark:#033f7a;
  --nav-top:#1a8fcf;
  --nav-bottom:#02427c;
  --purple:#a54599;
  --purple-dark:#6e1d66;
  --page-grey:#ececee;
  --footer-grey:#ededee;
  --text:#333;
  --muted:#555;
  --light-text:#777;
  --white:#fff;
}
*{margin:0;padding:0;box-sizing:border-box}
html,body{width:911px;height:1200px;overflow:hidden}
body{position:relative;background:var(--white);font-family:"Open Sans",Arial,sans-serif;color:var(--text)}
.abs{position:absolute}
.top-band{left:0;top:0;width:911px;height:304px;background:var(--page-grey);border-top:1px solid var(--blue)}
.brand{left:77px;top:30px;display:flex;align-items:center;gap:8px}
.brand-mark{width:26px;height:26px;border-radius:50%;background:var(--blue)}
.brand-name{font-size:24px;font-weight:400;color:var(--blue);letter-spacing:1px}
.contact-item{display:flex;align-items:center;top:40px}
.contact-item svg{margin-right:14px}
.contact-lines{border-left:1px solid #d4d4d8;padding-left:10px;font-size:9px;line-height:16px;color:var(--light-text);letter-spacing:.3px}
.phone{left:418px}
.mail{left:630px}
.main-nav{left:76px;top:99px;width:759px;height:34px;display:flex;background:linear-gradient(var(--nav-top),var(--nav-bottom))}
.main-nav a{display:flex;align-items:center;justify-content:center;color:var(--white);text-decoration:none;font-size:11.5px;border-right:1px solid rgba(0,0,0,.25)}
.main-nav a:last-child{border-right:0}
.main-nav a.current{background:linear-gradient(#c85bba,var(--purple-dark))}
.hero{left:78px;top:142px;width:757px;height:332px;overflow:hidden}
.hero-photo{width:100%;height:100%;background:linear-gradient(100deg,#6d7a8c 0%,#a9b8cc 30%,#e4e8ee 55%,#cfd4da 75%,#a3a9b4 100%)}
.hero-arrow{top:147px}
.hero-caption{left:0;bottom:0;width:100%;height:44px;background:rgba(225,225,228,.78);display:flex;align-items:center;justify-content:space-between;padding:0 50px 0 47px}
.hero-caption p{font-size:14.5px;color:#222}
.btn{display:flex;align-items:center;justify-content:center;color:var(--white);text-decoration:none;border-radius:2px}
.btn-purple{background:linear-gradient(#c55ab8,var(--purple-dark))}
.btn-blue{background:linear-gradient(var(--nav-top),var(--nav-bottom))}
.read-more{width:111px;height:23px;font-size:12px}
.slide-dot{left:442px;top:484px;width:5px;height:5px;border-radius:50%;background:var(--blue)}
.section-title{left:0;width:911px;text-align:center;font-size:18px;font-weight:400;color:#222}
.section-title span{color:var(--blue)}
.services{left:74px;top:561px;width:763px;display:flex;justify-content:space-between}
.service{width:235px;text-align:center}
.service-img{width:168px;height:101px;margin:0 auto}
.img-finance{background:linear-gradient(135deg,#244a8e,#c9d6e6 60%,#3a64b0)}
.img-office{background:linear-gradient(90deg,#050608 40%,#1d6fa6 75%,#6ab7e0)}
.img-analysis{background:linear-gradient(135deg,#0a3a66,#1d6aa2 50%,#c8ccd2)}
.service h3{margin-top:16px;font-size:13.5px;font-weight:400;color:#222}
.service p{margin-top:4px;font-size:9.9px;line-height:14px;color:var(--muted);text-align:justify;text-align-last:center}
.about-text{left:84px;top:826px;width:753px;font-size:9.5px;line-height:13.8px;color:#333;text-align:center}
.about-actions{left:319px;top:913px;display:flex;gap:7px}
.about-actions .btn{width:132px;height:26px;font-size:10px}
.site-footer{left:0;top:1008px;width:911px;height:155px;background:var(--footer-grey);border-top:1px solid #dcdcdf}
.footer-divider{left:304px;top:1008px;width:3px;height:157px;background:#d0d0d3}
.footer-contact{left:82px;top:1048px}
.fc-row{display:flex;align-items:center;height:29px}
.fc-icon{width:28px;height:28px;display:flex;align-items:center;justify-content:center;background:#b4b4b8}
.fc-icon.active{background:var(--blue)}
.fc-row span{margin-left:12px;font-size:10px;color:#333}
.fc-row span.link{text-decoration:underline}
.footer-col{top:1040px}
.footer-col h4{font-size:14px;font-weight:400;color:var(--blue);margin-bottom:4px}
.footer-col li{list-style:none;font-size:9.6px;line-height:19.7px;color:#444}
.footer-col li.current{color:var(--blue);text-decoration:underline}
.legal-bar{left:0;top:1163px;width:911px;height:37px;background:var(--blue);color:var(--white);font-size:10px;display:flex;align-items:center;padding:0 73px 0 83px}
.legal-bar nav{display:flex;gap:24px}
.legal-bar a{color:var(--white);text-decoration:none}
.legal-bar a.current{text-decoration:underline}
.legal-bar p{margin-left:auto}
</style>
</head>
<body>
<div class="abs top-band"></div>

<header>
  <div class="abs brand">
    <span class="brand-mark"></span>
    <span class="brand-name">TR Solutions</span>
  </div>
  <div class="abs contact-item phone">
    <svg width="14" height="20" viewBox="0 0 14 20"><path d="M3 1 L6 1 L7 6 L5 7 Q6 12 10 15 L12 13 L14 17 L12 19 Q2 16 1 4 Z" fill="#a54599"/></svg>
    <div class="contact-lines">+61-4-12345678 (intl)<br>0412 345 678 (within Australia)</div>
  </div>
  <div class="abs contact-item mail">
    <svg width="22" height="15" viewBox="0 0 22 15"><rect x="0.5" y="0.5" width="21" height="14" fill="#0555a3"/><path d="M1 1 L11 9 L21 1 M1 14 L8 7 M21 14 L14 7" stroke="#fff" stroke-width="1" fill="none"/></svg>
    <div class="contact-lines">administrator@tr-solutions.com<br>info@trsolutions-mail.com</div>
  </div>
  <nav class="abs main-nav">
    <a class="current" href="#" style="width:122px">Home</a>
    <a href="#" style="width:128px">About Us</a>
    <a href="#" style="width:123px">Service</a>
    <a href="#" style="width:106px">News</a>
    <a href="#" style="width:151px">Testimonials</a>
    <a href="#" style="width:129px">Contact Us</a>
  </nav>
</header>

<section class="abs hero">
  <div class="hero-photo" role="img" aria-label="Photo of business professionals in a bright office meeting"></div>
  <svg class="abs hero-arrow" style="left:14px" width="22" height="22" viewBox="0 0 22 22"><circle cx="11" cy="11" r="11" fill="#555" opacity=".75"/><path d="M13 6 L8 11 L13 16" stroke="#ddd" stroke-width="2" fill="none"/></svg>
  <svg class="abs hero-arrow" style="left:719px" width="22" height="22" viewBox="0 0 22 22"><circle cx="11" cy="11" r="11" fill="#555" opacity=".75"/><path d="M9 6 L14 11 L9 16" stroke="#ddd" stroke-width="2" fill="none"/></svg>
  <div class="abs hero-caption">
    <p>Lorem ipsum dolor sit amet, consectetur adipiscing elit. Nulla bibendum</p>
    <a class="btn btn-purple read-more" href="#">Read More</a>
  </div>
</section>
<span class="abs slide-dot"></span>

<h2 class="abs section-title" style="top:520px">We <span>Specialise in</span></h2>
<section class="abs services">
  <article class="service">
    <div class="service-img img-finance" role="img" aria-label="Photo of a person working at a computer keyboard"></div>
    <h3>Business Finance Solutions</h3>
    <p>Duis dictum elit quis velit ornare mattis. Nullam non dui leo. Etiam rhoncus egestas rutrum. Morbi sed velit tincidunt, elementum ipsum quis.</p>
  </article>
  <article class="service">
    <div class="service-img img-office" role="img" aria-label="Illustration of office file icons flowing along arrows"></div>
    <h3>Spreadsheet Automation</h3>
    <p>Duis dictum elit quis velit ornare mattis. Nullam non dui leo. Etiam rhoncus egestas rutrum. Morbi sed velit tincidunt, elementum ipsum quis.</p>
  </article>
  <article class="service">
    <div class="service-img img-analysis" role="img" aria-label="Illustration of data analysis charts"></div>
    <h3>Programming And Data Analysis</h3>
    <p>Duis dictum elit quis velit ornare mattis. Nullam non dui leo. Etiam rhoncus egestas rutrum. Morbi sed velit tincidunt, elementum ipsum quis.</p>
  </article>
</section>

<h2 class="abs section-title" style="top:780px">About <span>TR Solution</span></h2>
<p class="abs about-text">Pellentesque nec scelerisque sem. Pellentesque dapibus mattis tellus, a sagittis ipsum iaculis eget. Praesent hendrerit felis sed diam feugiat, nec tristique metus faucibus. Proin feugiat luctus turpis id fermentum. Curabitur pulvinar iaculis metus dapibus sagittis. Vestibulum fringilla leo imperdiet eleifend placerat. Ut dapibus elit neque, sed facilisis orci lobortis sit amet. In hac habitasse platea dictumst. Nullam sed odio mollis, scelerisque magna quis, ullamcorper neque. Nunc vitae risus eget neque tincidunt aliquet eu eget est. Etiam consequat, neque ut condimentum mattis, massa nunc pulvinar nulla, sed dictum urna mi sit amet</p>
<div class="abs about-actions">
  <a class="btn btn-purple" href="#">View Works</a>
  <a class="btn btn-blue" href="#">LEARN MORE!</a>
</div>

<footer>
  <div class="abs site-footer"></div>
  <div class="abs footer-divider"></div>
  <div class="abs footer-contact">
    <div class="fc-row"><div class="fc-icon active"><svg width="10" height="14" viewBox="0 0 10 14"><rect x="1" y="1" width="8" height="12" rx="1.5" fill="none" stroke="#fff" stroke-width="1.4"/><circle cx="5" cy="10.5" r=".9" fill="#fff"/></svg></div><span class="link">0412 345 678 (within Australia)</span></div>
    <div class="fc-row"><div class="fc-icon"><svg width="10" height="14" viewBox="0 0 10 14"><path d="M5 13 C1 8 1 6 1 5 A4 4 0 0 1 9 5 C9 6 9 8 5 13 Z" fill="none" stroke="#fff" stroke-width="1.3"/><circle cx="5" cy="5" r="1.3" fill="#fff"/></svg></div><span>1820 Elm Ave., Springfield</span></div>
    <div class="fc-row"><div class="fc-icon"><svg width="13" height="10" viewBox="0 0 13 10"><rect x=".7" y=".7" width="11.6" height="8.6" fill="none" stroke="#fff" stroke-width="1.2"/><path d="M1 1 L6.5 5.5 L12 1" fill="none" stroke="#fff" stroke-width="1.2"/></svg></div><span>administrator@tr-solutions.com</span></div>
  </div>
  <div class="abs footer-col" style="left:351px"><h4>About</h4><ul><li class="current">Vivamus sagittis</li><li>lacus vel augue cibus</li><li>laoreet rutrum</li></ul></div>
  <div class="abs footer-col" style="left:478px"><h4>Topics</h4><ul><li>Fringilla Cursus</li><li>Fusce Tortor Commodo</li><li>Euismod Aenean</li><li>Mattis Bibendum</li></ul></div>
  <div class="abs footer-col" style="left:606px"><h4>Community</h4><ul><li>Mattis Amet</li><li>Lorem</li><li>Consectetur</li></ul></div>
  <div class="abs footer-col" style="left:731px"><h4>Schedule</h4><ul><li>Justo Adipiscing Purus</li><li>Mollis Parturient</li><li>Egestas</li><li>Parturient Ullamcorper</li></ul></div>
  <div class="abs legal-bar">
    <nav><a class="current" href="#">Terms of use</a><a href="#">Privacy policy</a><a href="#">FAQs</a></nav>
    <p>yoursite © 2014 &nbsp;All Rights Reserved</p>
  </div>
</footer>
</body>
</html>
```